Business Card for new Architectural Firm

I intend to practice in a rural mountain community in upstate NY, focusing on residential and light commercial projects, including second home / vacation properties. I wish to convey a feeling of rural outdoorsy modernity.

Color is important - bold and urbane. Secondary or tertiary colors preferred.

Font is important, idiosyncratic is ok

Optionally, I may choose to use the name Brambleford Studio. If used as part of your design, all of the Must Haves are still required.

Images uploaded are logos I like

Industry/Entity Type

Residential

Contact Information for Business Card

Calvin Worthaven
Architect (This word should stand alone or be associated with my name - not license number)
NY License No. 052816
calvin@designbycw.com
607 385 2194

Font styles to use
Sans Serif
Decorative

Requirements
Must have
• Whatever files I need to best utilize your design
• PDF
• JPG
• EPS
• Vectorwhatsit
Nice to have
• Logo or element that can be incorporated into other print material.
• Could be a font based card
Should not have
• no clip art
• No templates
• no floor plans
• no building photographs

```html
<!DOCTYPE html>
<html lang="en">
<head>
<meta charset="utf-8">
<title>Calvin Worthaven Architect – Business Card</title>
<link rel="stylesheet" href="https://fonts.googleapis.com/css2?family=Roboto:wght@300;400&display=swap">
<style>
  :root {
    --backdrop: #2b2b2b;
    --card: #f7f7f7;
    --card-edge: #ececec;
    --name-blue: #5b86c5;
    --leaf-green: #5fae3e;
    --band-text: #ffffff;
  }
  html, body {
    margin: 0;
    padding: 0;
    width: 1200px;
    height: 900px;
    overflow: hidden;
    background: var(--backdrop);
  }
  .card {
    position: absolute;
    left: 100px;
    top: 164px;
    width: 1000px;
    height: 571px;
    background: radial-gradient(ellipse at 50% 25%, #ffffff 0%, var(--card) 55%, var(--card-edge) 100%);
    font-family: "Roboto", "Helvetica Neue", Arial, sans-serif;
  }
  .identity {
    position: absolute;
    left: 109px;
    top: 229px;
    display: flex;
    align-items: center;
  }
  .identity-square {
    width: 104px;
    height: 104px;
    background: var(--leaf-green);
    margin-right: 30px;
  }
  .identity-text {
    display: flex;
    flex-direction: column;
  }
  .name {
    font-weight: 300;
    font-size: 58px;
    line-height: 1;
    color: var(--name-blue);
    letter-spacing: 1px;
  }
  .title {
    margin-top: 12px;
    font-weight: 300;
    font-size: 26px;
    line-height: 1;
    color: var(--leaf-green);
    letter-spacing: 36px;
  }
  .contact-band {
    position: absolute;
    left: 0;
    right: 0;
    bottom: 0;
    height: 107px;
    background: var(--leaf-green);
    color: var(--band-text);
    display: flex;
    flex-direction: column;
    align-items: center;
    justify-content: center;
    font-weight: 300;
    font-size: 24px;
    letter-spacing: 1px;
    line-height: 1.4;
  }
  .contact-line {
    display: flex;
    align-items: center;
    gap: 10px;
  }
  .divider { margin: 0 6px; }
  .icon { width: 22px; height: 16px; fill: var(--band-text); }
</style>
</head>
<body>
  <div class="card">
    <div class="identity">
      <div class="identity-square"></div>
      <div class="identity-text">
        <div class="name">Calvin Worthaven</div>
        <div class="title">ARCHITECT</div>
      </div>
    </div>
    <div class="contact-band">
      <div class="contact-line">
        <svg class="icon" viewBox="0 0 22 16" aria-hidden="true">
          <path d="M2 5 C2 1 20 1 20 5 L16 6 L15 4 C12 3 10 3 7 4 L6 6 Z"/>
          <path d="M6 7 L16 7 L19 14 L3 14 Z"/>
        </svg>
        <span>607 385 2194</span>
        <span class="divider">|</span>
        <svg class="icon" viewBox="0 0 22 16" aria-hidden="true">
          <path d="M2 3 H20 V14 H2 Z M3 4 L11 10 L19 4" fill="none" stroke="#ffffff" stroke-width="1.6"/>
        </svg>
        <span>calvin@designbycw.com</span>
      </div>
      <div class="contact-line">NY License No. 052816</div>
    </div>
  </div>
</body>
</html>
```